Elevating our current Business Card Design

We want to elevate our current business card with a new design to look like a zenith 300 company. We are a premium lubricant distributor (oil and grease).
We need 2 versions, version 1 is as per the uploaded a copy of our current business card with the English version.
For our Chinese version we need to use the front to be English in English and have the back of the card designed exactly like the front for all info to be in Chinese.
The design template needs to be such that we can amend the template with adding different information for each person's card.
The background colour of the card can be changed- we just need to clearly see all information on the card and logos.
The QJR and Ember steady logos cannot have any colour or display changes- only use the logos attached.
All logos need to be included and all information from the attached current card

```html
<!DOCTYPE html>
<html lang="en">
<head>
<meta charset="utf-8">
<title>KELVA Business Card</title>
<link rel="stylesheet" href="https://fonts.googleapis.com/css2?family=Montserrat:wght@400;500;700;800&display=swap">
<style>
  :root {
    --brand-red: #ee2e24;
    --accent-yellow: #f2b227;
    --card-white: #ffffff;
    --card-dark: #141414;
    --stage: #1c1c1c;
    --ink: #1d1d1d;
    --badge-grey: #d9d9d9;
    --badge-green: #1c4b36;
  }
  * { box-sizing: border-box; margin: 0; padding: 0; }
  html, body { width: 1200px; height: 1059px; overflow: hidden; }
  body {
    background: var(--stage);
    font-family: "Montserrat", sans-serif;
    position: relative;
  }
  .card {
    position: absolute;
    border-radius: 22px;
    overflow: hidden;
  }
  .card--front { left: 257px; top: 86px; width: 688px; height: 400px; background: var(--card-white); }
  .card--back { left: 252px; top: 546px; width: 710px; height: 401px; background: var(--card-dark); }

  .contact-band {
    position: absolute; left: 0; right: 0; top: 234px; bottom: 0;
    background: var(--brand-red);
  }
  .cert-badge {
    position: absolute; left: 38px; top: 20px; width: 108px; height: 104px;
    border-radius: 8px; background: var(--badge-grey);
  }

  .brand-mark {
    position: absolute; left: 320px; top: 30px; width: 345px;
    display: flex; align-items: center; justify-content: flex-end; gap: 12px;
  }
  .brand-mark__dot { flex: none; width: 34px; height: 34px; border-radius: 50%; background: var(--accent-yellow); }
  .brand-mark__name {
    font-weight: 800; font-size: 86px; letter-spacing: 2px; color: var(--brand-red); line-height: 1;
  }

  .name-accent { position: absolute; left: 0; top: 149px; width: 18px; height: 43px; background: var(--brand-red); }
  .person { position: absolute; left: 44px; top: 148px; }
  .person__name { font-weight: 700; font-size: 25px; color: var(--brand-red); line-height: 1.2; }
  .person__title { font-weight: 500; font-size: 15px; color: var(--ink); margin-top: 1px; }

  .partner-strip { position: absolute; left: 404px; top: 192px; width: 284px; height: 42px; }
  .partner-strip__bg { position: absolute; inset: 0; }
  .partner-tab {
    position: absolute; left: 10px; top: 4px; width: 144px; height: 34px;
    display: flex; align-items: center; gap: 6px; padding-left: 10px;
  }
  .partner-tab__name { font-weight: 800; font-size: 15px; color: var(--brand-red); }
  .partner-tab__caption { font-size: 6.5px; line-height: 1.15; color: var(--brand-red); font-weight: 500; }
  .supplier { position: absolute; left: 170px; top: 6px; color: var(--card-white); text-align: center; }
  .supplier__name { font-weight: 800; font-size: 18px; line-height: 1; }
  .supplier__tag { font-weight: 700; font-size: 7.5px; letter-spacing: .3px; }

  .contact-list { position: absolute; left: 37px; top: 264px; list-style: none; }
  .contact-list li {
    display: flex; align-items: center; gap: 17px; height: 24.5px;
    font-size: 14.5px; color: var(--card-white);
  }
  .contact-list svg { width: 18px; height: 18px; fill: var(--accent-yellow); flex: none; }

  .network-badge {
    position: absolute; left: 538px; top: 268px; width: 92px; height: 66px;
    border-radius: 8px; background: var(--badge-green);
  }
  .address {
    position: absolute; left: 479px; top: 352px;
    font-size: 14px; line-height: 1.2; color: var(--card-white);
  }

  .back-mark {
    position: absolute; inset: 0;
    display: flex; align-items: center; justify-content: center; gap: 22px;
  }
  .back-mark__dot { flex: none; width: 54px; height: 54px; border-radius: 50%; background: var(--accent-yellow); }
  .back-mark__name { font-weight: 800; font-size: 140px; letter-spacing: 3px; color: var(--brand-red); line-height: 1; }
</style>
</head>
<body>

<section class="card card--front" aria-label="Card front">
  <div class="cert-badge" role="img" aria-label="QJR certification badge"></div>

  <div class="brand-mark">
    <span class="brand-mark__dot"></span>
    <span class="brand-mark__name">KELVA</span>
  </div>

  <div class="name-accent"></div>
  <div class="person">
    <p class="person__name">Marina Costa</p>
    <p class="person__title">Administraction Executive</p>
  </div>

  <div class="contact-band"></div>

  <div class="partner-strip">
    <svg class="partner-strip__bg" viewBox="0 0 284 42" preserveAspectRatio="none">
      <polygon points="8,0 284,0 284,42 0,42" fill="var(--brand-red)"/>
      <polygon points="14,2 158,2 154,40 8,40" fill="var(--card-white)"/>
    </svg>
    <div class="partner-tab">
      <span class="partner-tab__name">KELVA</span>
      <span class="partner-tab__caption">MERIDIAN<br>LUBRICANT<br>DISTRIBUTORS</span>
    </div>
    <div class="supplier">
      <p class="supplier__name">NORVEX</p>
      <p class="supplier__tag">PREMIUM LUBRICANTS</p>
    </div>
  </div>

  <ul class="contact-list">
    <li><svg viewBox="0 0 20 20"><path d="M2 7c0-3 4-4 8-4s8 1 8 4v2h-4V7H6v2H2z M5 10h10l2 8H3z"/><circle cx="10" cy="14" r="2" fill="var(--brand-red)"/></svg>1300 555 014</li>
    <li><svg viewBox="0 0 20 20"><rect x="5" y="1" width="10" height="18" rx="2"/><rect x="7" y="4" width="6" height="10" fill="var(--brand-red)"/></svg>+16 400 555 218</li>
    <li><svg viewBox="0 0 20 20"><rect x="6" y="1" width="8" height="6"/><rect x="2" y="7" width="16" height="8" rx="1"/><rect x="6" y="12" width="8" height="7" stroke="var(--brand-red)" stroke-width="1"/></svg>+16 8 5550 1234</li>
    <li><svg viewBox="0 0 20 20"><rect x="1" y="4" width="18" height="12" rx="1"/><path d="M1 5l9 6 9-6" stroke="var(--brand-red)" stroke-width="1.5" fill="none"/></svg>marina.costa@kelvadirect.com</li>
    <li><svg viewBox="0 0 20 20"><circle cx="10" cy="10" r="9"/><path d="M4 6c3 0 3 3 5 3s1 4 3 4M12 3c0 3 3 3 5 5" stroke="var(--brand-red)" stroke-width="1.5" fill="none"/></svg>www.kelvadirect.com</li>
  </ul>

  <div class="network-badge" role="img" aria-label="Ember steady network member badge"></div>

  <p class="address">48 Harbour Freight Road<br>Brayfield, WA 6190</p>
</section>

<section class="card card--back" aria-label="Card back">
  <div class="back-mark">
    <span class="back-mark__dot"></span>
    <span class="back-mark__name">KELVA</span>
  </div>
</section>

</body>
</html>
```